Professional & attention grabbing.

A business card design, front and back. I already have a logo I will attach, but I am open to something new as well.
Things to include:
Name:
Title:
Phone:
Email:
Wanting something that is professional but attention grabbing.
Also we do a lot of work using drones on natural gas pipelines (leading the future)if you want to include any of that. I'm open to ideas.
Target Market(s)
Natural gas transmission industry / greenhouse gas mitigation industry
Industry/Entity Type
Business
Colors
Designer to choose colors to be used in the design.
Look and feel
Each slider illustrates characteristics of the customer's brand and the style your logo design should communicate.

```html
<!DOCTYPE html>
<html lang="en">
<head>
<meta charset="utf-8">
<title>Kestrel Line Inspection – Business Card</title>
<link href="https://fonts.googleapis.com/css2?family=Open+Sans:wght@400;600;700&display=swap" rel="stylesheet">
<style>
  :root {
    --orange: #e07308;
    --orange-light: #e98a2e;
    --grey: #7f7f7f;
    --white: #ffffff;
    --backdrop: #ecebe8;
  }
  * { box-sizing: border-box; margin: 0; padding: 0; }
  html, body { width: 1200px; height: 900px; overflow: hidden; }
  body {
    background: var(--backdrop);
    font-family: "Open Sans", Arial, sans-serif;
    position: relative;
  }
  .card {
    position: absolute;
    overflow: hidden;
    box-shadow: 0 6px 18px rgba(0,0,0,0.18);
  }
  /* Front */
  .card-front {
    left: 78px; top: 34px; width: 588px; height: 364px;
    background: var(--white);
  }
  .card-front .bands { position: absolute; inset: 0; }
  .brand {
    position: absolute; left: 160px; top: 70px;
    display: flex; align-items: center; gap: 14px;
    color: var(--orange); font-weight: 700;
    font-size: 30px; letter-spacing: 1px;
  }
  .brand-square { width: 34px; height: 34px; background: var(--orange); }
  .person {
    position: absolute; right: 313px; top: 262px; text-align: right;
    color: var(--white);
  }
  .person-name { font-size: 19px; font-weight: 700; line-height: 1.2; letter-spacing: 0.3px; }
  .person-title { font-size: 15px; font-weight: 400; line-height: 1.3; }
  .divider {
    position: absolute; left: 293px; top: 264px;
    width: 1.5px; height: 40px; background: var(--white);
  }
  .contacts {
    position: absolute; left: 311px; top: 263px;
    color: var(--white); font-size: 15px; line-height: 22px;
    list-style: none;
  }
  .contacts li { display: flex; align-items: center; gap: 6px; }
  .contacts svg { width: 13px; height: 13px; fill: var(--white); }
  .address {
    position: absolute; left: 110px; top: 322px;
    color: var(--white); font-size: 15px;
  }
  /* Back */
  .card-back {
    left: 388px; top: 505px; width: 567px; height: 352px;
    background: var(--orange);
  }
  .back-pattern {
    position: absolute; inset: 0;
    background: linear-gradient(135deg, var(--orange-light), var(--orange));
  }
  .back-brand {
    position: absolute; left: 0; right: 0; top: 152px;
    display: flex; justify-content: center; align-items: center; gap: 12px;
    color: var(--white); font-weight: 700; font-size: 26px; letter-spacing: 1px;
  }
  .back-brand .brand-square { width: 30px; height: 30px; background: var(--white); }
  .web {
    position: absolute; left: 0; right: 0; top: 294px; text-align: center;
    color: var(--white); font-size: 15px;
  }
</style>
</head>
<body>
  <section class="card card-front" aria-label="Business card front">
    <svg class="bands" width="588" height="364" viewBox="0 0 588 364">
      <polygon points="0,199 400,199 377,225 0,225" fill="var(--grey)"/>
      <polygon points="0,228 382,228 414,191 588,191 588,364 0,364" fill="var(--orange)"/>
    </svg>
    <div class="brand"><span class="brand-square"></span>KESTREL LINE</div>
    <div class="person">
      <p class="person-name">DANIEL MORROW</p>
      <p class="person-title">Managing Director</p>
    </div>
    <span class="divider"></span>
    <ul class="contacts">
      <li><svg viewBox="0 0 24 24"><path d="M6.6 10.8a15.1 15.1 0 0 0 6.6 6.6l2.2-2.2c.3-.3.7-.4 1-.2 1.1.4 2.3.6 3.6.6.6 0 1 .4 1 1V20c0 .6-.4 1-1 1C10.6 21 3 13.4 3 4c0-.6.4-1 1-1h3.5c.6 0 1 .4 1 1 0 1.3.2 2.5.6 3.6.1.3 0 .7-.2 1z"/></svg>(055)987654321</li>
      <li><svg viewBox="0 0 24 24"><path d="M2 5h20v14H2z M2 5l10 8 10-8" fill="var(--white)" stroke="var(--orange)" stroke-width="1.5"/></svg>hello@kestrelline.com</li>
    </ul>
    <p class="address">48 Ridgeway Court, Harbor Falls, Northland, 204816.</p>
  </section>

  <section class="card card-back" aria-label="Business card back">
    <div class="back-pattern" role="img" aria-label="Repeating brand pattern in light orange tiles"></div>
    <div class="back-brand"><span class="brand-square"></span>KESTREL LINE</div>
    <p class="web">www.kestrelline.com</p>
  </section>
</body>
</html>
```